Finding the Root: Reason in Clinical Choice-Crafting

I'd like a cover that looks like it would fit on the shelf next to "The Illness Mirage" by Corwin Talley, "The Close of Forgetting" by Hugh Marchetti, "Meal Mend" by Paul Grieve, "The Energy Restart Plan" by Oscar Pemberley or "The Gland Restart Plan" by the same or "The Cortex Restart Plan" by the same ... either text only (with some interesting fonts that make the title stand out, and the subtitle smaller) or a relevant image, though I'm not entirely sure what that would be since this is a book about big-picture medical decision making.
Author name is Dr Tessa Morrow, NMD
I'll eventually request an e-book, paperback, and audio cover from the winner...

Target Market(s)

practicing physicians

Industry/Entity Type

medicine

Requirements
Must have
• look similar to other books in the genre

```html
<!DOCTYPE html>
<html lang="en">
<head>
<meta charset="UTF-8">
<title>Finding the Root — Book Cover</title>
<link href="https://fonts.googleapis.com/css2?family=Playfair+Display:wght@700;900&family=Josefin+Sans:wght@400;600&family=Allura&display=swap" rel="stylesheet">
<style>
  :root {
    --backdrop: #f1d9c8;
    --paper: #f4f3ef;
    --navy: #3d5570;
    --green: #76995c;
    --rule: #b9bcbc;
  }
  * { margin: 0; padding: 0; box-sizing: border-box; }
  html, body {
    width: 1200px;
    height: 900px;
    overflow: hidden;
    background: var(--backdrop);
  }
  .stage {
    width: 1200px;
    height: 900px;
    display: flex;
    align-items: center;
    justify-content: center;
  }
  .cover {
    position: relative;
    width: 566px;
    height: 840px;
    background: var(--paper);
    display: flex;
    flex-direction: column;
    align-items: center;
    padding-top: 52px;
    color: var(--navy);
  }
  .tagline {
    font-family: "Josefin Sans", sans-serif;
    font-size: 14px;
    letter-spacing: 0.22em;
    line-height: 1.55;
    text-align: center;
    text-transform: uppercase;
  }
  .rule {
    height: 1px;
    background: var(--rule);
  }
  .rule--top { width: 360px; margin-top: 22px; }
  .title {
    position: relative;
    display: flex;
    flex-direction: column;
    align-items: center;
    margin-top: 30px;
    text-transform: uppercase;
  }
  .title__lead {
    font-family: "Josefin Sans", sans-serif;
    font-weight: 600;
    font-size: 36px;
    line-height: 1;
    letter-spacing: 0.26em;
    padding-left: 0.26em;
  }
  .title__root {
    font-family: "Playfair Display", serif;
    font-weight: 900;
    font-size: 160px;
    line-height: 0.8;
    letter-spacing: -0.02em;
    margin-top: 14px;
  }
  .title__script {
    position: absolute;
    left: 50%;
    top: 108px;
    transform: translateX(-46%) rotate(-8deg);
    font-family: "Allura", cursive;
    font-size: 120px;
    line-height: 1;
    color: var(--green);
    text-transform: none;
    white-space: nowrap;
  }
  .title__middle {
    font-family: "Josefin Sans", sans-serif;
    font-weight: 600;
    font-size: 34px;
    line-height: 1;
    letter-spacing: 0.24em;
    padding-left: 0.24em;
    margin-top: 88px;
  }
  .title__end {
    font-family: "Josefin Sans", sans-serif;
    font-weight: 600;
    font-size: 38px;
    line-height: 1;
    letter-spacing: 0.14em;
    padding-left: 0.14em;
    color: var(--green);
    margin-top: 14px;
  }
  .rule--mid { width: 400px; margin-top: 34px; }
  .subtitle {
    font-family: "Josefin Sans", sans-serif;
    font-size: 16px;
    letter-spacing: 0.2em;
    line-height: 1.55;
    text-align: center;
    text-transform: uppercase;
    margin-top: 26px;
  }
  .divider {
    display: flex;
    align-items: center;
    gap: 14px;
    margin-top: 28px;
  }
  .divider .rule { width: 60px; }
  .divider__mark {
    width: 18px;
    height: 14px;
    border-radius: 50%;
    background: var(--green);
  }
  .author {
    font-family: "Playfair Display", serif;
    font-weight: 700;
    font-size: 36px;
    margin-top: 24px;
  }
</style>
</head>
<body>
<main class="stage">
  <article class="cover">
    <p class="tagline">Make confident, informed choices.<br>Get better. Stay better.</p>
    <div class="rule rule--top"></div>

    <h1 class="title">
      <span class="title__lead">Finding the</span>
      <span class="title__root">ROOT</span>
      <span class="title__script">Reason</span>
      <span class="title__middle">in Clinical</span>
      <span class="title__end">Choice-Crafting</span>
    </h1>

    <div class="rule rule--mid"></div>
    <p class="subtitle">A practical guide to<br>root cause medicine and<br>smarter medical decisions</p>

    <div class="divider">
      <span class="rule"></span>
      <span class="divider__mark" role="img" aria-label="Small green leaf ornament"></span>
      <span class="rule"></span>
    </div>

    <p class="author">Dr Tessa Morrow, NMD</p>
  </article>
</main>
</body>
</html>
```